Post storm repair flyer

looking for an eye catching 6x9 postcard to send out to single family home owners advertising a "Post Storm Repair Special" explaining that after the recent hurricanes its very important to have your roof checked and any repairs fixed right away before they become a bigger more costly problem and that even though your home wasn't directly hit by the storm the high wind gust could've cause unseen damage.
offer $200 off any repair *some rules may apply
Crest Roofing
877.512.DUNE
www.DuneRoofingco.example

```html
<!DOCTYPE html>
<html lang="en">
<head>
<meta charset="utf-8">
<title>Crest Roofing – Post Storm Repair Postcard</title>
<link rel="stylesheet" href="https://fonts.googleapis.com/css2?family=Anton&family=Allison&family=Montserrat:wght@500;600;700&family=Poppins:wght@400&display=swap">
<style>
  :root {
    --page-bg: #d3d3d3;
    --card-dark: #161616;
    --card-mid: #3c3c3c;
    --card-light: #6a6a6a;
    --gold: #e6b425;
    --gold-deep: #c99a14;
    --white: #f2f2f2;
    --text-soft: #e4e4e4;
    --band: rgba(255,255,255,0.08);
    --sky-top: #6d9bb6;
    --sky-bottom: #4d7f9c;
    --roof: #2b5168;
    --storm-top: #6b6a63;
    --storm-bottom: #5a4a33;
  }
  * { box-sizing: border-box; margin: 0; padding: 0; }
  html, body { width: 803px; height: 1200px; overflow: hidden; background: var(--page-bg); }
  .canvas { position: relative; width: 803px; height: 1200px; }

  .postcard {
    position: absolute;
    left: 31px;
    width: 741px;
    height: 494px;
    overflow: hidden;
    background:
      radial-gradient(ellipse at 62% 55%, rgba(140,140,140,0.55), transparent 60%),
      linear-gradient(125deg, var(--card-dark) 0%, var(--card-mid) 45%, var(--card-light) 62%, var(--card-mid) 78%, var(--card-dark) 100%);
  }
  .postcard--front { top: 34px; }
  .postcard--back { top: 617px; }

  .edge-band { position: absolute; left: 0; right: 0; height: 20px; background: var(--band); }
  .edge-band--top { top: 0; }
  .edge-band--bottom { bottom: 0; }

  .brand {
    position: absolute;
    display: flex; align-items: center; gap: 10px;
    font-family: "Montserrat", sans-serif;
    font-weight: 600;
    color: var(--white);
    letter-spacing: 0.04em;
    text-transform: uppercase;
  }
  .brand__square { display: block; background: var(--white); }

  .url {
    position: absolute;
    font-family: "Montserrat", sans-serif;
    font-weight: 500;
    color: var(--white);
    letter-spacing: 0.02em;
    white-space: nowrap;
  }

  /* Front */
  .front .brand { left: 117px; top: 88px; transform: translateX(-50%); font-size: 20px; white-space: nowrap; }
  .front .brand__square { width: 14px; height: 14px; }
  .front .url { left: 198px; top: 133px; transform: translateX(-50%); font-size: 16px; }

  .headline {
    position: absolute; left: 25px; top: 170px;
    font-family: "Anton", sans-serif;
    color: var(--gold);
    font-size: 59px; line-height: 60px;
    letter-spacing: 0.005em;
    text-transform: uppercase;
  }
  .body-copy {
    position: absolute; left: 25px; width: 420px;
    font-family: "Poppins", sans-serif;
    font-size: 12.2px; line-height: 15.2px;
    color: var(--text-soft);
  }
  .body-copy--first { top: 303px; }
  .body-copy--second { top: 365px; }

  .offer {
    position: absolute; left: 25px; top: 410px;
    font-family: "Anton", sans-serif;
    font-size: 26px; line-height: 30px;
    color: var(--gold);
    text-transform: uppercase;
  }
  .offer__note {
    position: absolute; left: 25px; top: 442px;
    font-family: "Montserrat", sans-serif;
    font-weight: 700; font-size: 8.5px;
    color: var(--white);
    letter-spacing: 0.03em;
    text-transform: uppercase;
  }

  .call {
    position: absolute; text-align: center;
  }
  .call__script {
    display: block;
    font-family: "Allison", cursive;
    color: var(--white);
    line-height: 1;
  }
  .call__phone {
    display: block;
    font-family: "Anton", sans-serif;
    color: var(--gold);
    line-height: 1;
  }
  .front .call { left: 574px; top: 350px; width: 190px; }
  .front .call__script { font-size: 82px; margin-left: -12px; }
  .front .call__phone { font-size: 27px; margin-top: -22px; }

  .visual { position: absolute; top: 0; right: 0; width: 741px; height: 494px; pointer-events: none; }

  /* Back */
  .back .brand { left: 50%; top: 126px; transform: translateX(-50%); font-size: 34px; white-space: nowrap; }
  .back .brand__square { width: 24px; height: 24px; }
  .back .url { left: 50%; top: 241px; transform: translateX(-50%); font-size: 27px; }
  .back .call { left: 50%; top: 306px; width: 260px; transform: translateX(-50%); }
  .back .call__script { font-size: 96px; }
  .back .call__phone { font-size: 31px; margin-top: -24px; }
</style>
</head>
<body>
<main class="canvas">

  <section class="postcard postcard--front front" aria-label="Postcard front">
    <div class="edge-band edge-band--top"></div>
    <div class="edge-band edge-band--bottom"></div>

    <svg class="visual" viewBox="0 0 741 494" aria-hidden="false">
      <defs>
        <linearGradient id="sky" x1="0" y1="0" x2="0" y2="1">
          <stop offset="0" stop-color="var(--sky-top)"/>
          <stop offset="0.55" stop-color="var(--sky-bottom)"/>
          <stop offset="1" stop-color="var(--roof)"/>
        </linearGradient>
        <linearGradient id="storm" x1="0" y1="0" x2="0" y2="1">
          <stop offset="0" stop-color="var(--storm-top)"/>
          <stop offset="1" stop-color="var(--storm-bottom)"/>
        </linearGradient>
      </defs>
      <polygon class="frame-gold" points="401,0 741,0 741,201 575,262 401,145" fill="var(--gold-deep)"/>
      <polygon class="frame-gold-light" points="413,0 741,0 741,190 575,250 413,139" fill="var(--gold)"/>
      <polygon class="frame-white" points="414,0 741,0 741,184 575,244 414,134" fill="var(--white)"/>
      <polygon class="photo-roofer" points="426,0 741,0 741,170 575,230 426,130" fill="url(#sky)"
               role="img" aria-label="Photo of a roofer in a hard hat working on a tiled roof under a blue sky"/>
      <polygon class="hex-frame" points="575,153 634,186 634,252 575,285 516,252 516,186" fill="var(--white)"/>
      <polygon class="photo-storm" points="575,160 628,190 628,248 575,278 522,248 522,190" fill="url(#storm)"
               role="img" aria-label="Photo of a tornado touching down over a grassy field"/>
    </svg>

    <div class="brand"><span class="brand__square"></span>Crest Roofing</div>
    <div class="url">DUNEROOFINGCO.EXAMPLE</div>

    <h1 class="headline">Post Storm<br>Repair Special</h1>

    <p class="body-copy body-copy--first">After the recent hurricanes its very important to have your roof checked and any repairs fixed right away before they become a bigger more costly problem</p>
    <p class="body-copy body-copy--second">Even though your home wasn't directly hit by the storm the high wind gust could've cause unseen damage.</p>

    <p class="offer">$200 Off Any Repair</p>
    <p class="offer__note">*Some rules may apply</p>

    <div class="call">
      <span class="call__script">Call us</span>
      <span class="call__phone">877.512.DUNE</span>
    </div>
  </section>

  <section class="postcard postcard--back back" aria-label="Postcard back">
    <div class="edge-band edge-band--top"></div>
    <div class="edge-band edge-band--bottom"></div>

    <div class="brand"><span class="brand__square"></span>Crest Roofing</div>
    <div class="url">DUNEROOFINGCO.EXAMPLE</div>

    <div class="call">
      <span class="call__script">Call us</span>
      <span class="call__phone">877.512.DUNE</span>
    </div>
  </section>

</main>
</body>
</html>
```